Business Cards for a law firm

Business cards for our law firm. Use our silhoette logo and OAK PARTNERS - check our website (www.oakpartners.example)

Contact Information for Business Card

our silhouette logo, OAK PARTNERS, 800-555-0147, Dorian Pemberton, dorian@oakpartners.example

Requirements
Must have
• our silhouette logo, OAK PARTNERS, 800-555-0147, Dorian Pemberton, dorian@oakpartners.example

```html
<!DOCTYPE html>
<html lang="en">
<head>
<meta charset="utf-8">
<title>Oak Partners – Business Cards</title>
<link rel="stylesheet" href="https://fonts.googleapis.com/css2?family=Open+Sans:ital,wght@0,400;0,600;1,400&display=swap">
<style>
  :root {
    --navy: #1f2d63;
    --paper: #f3f3f1;
    --gold: #e8a21f;
    --white: #ffffff;
    --backdrop: #d6d6d6;
  }
  * { box-sizing: border-box; margin: 0; padding: 0; }
  html, body { width: 1200px; height: 853px; overflow: hidden; }
  body {
    background: var(--backdrop);
    font-family: "Open Sans", Arial, sans-serif;
    display: flex;
    flex-direction: column;
    align-items: center;
    justify-content: center;
    gap: 36px;
  }
  .card {
    position: relative;
    width: 660px;
    height: 377px;
    border-radius: 26px;
    background: var(--navy);
    color: var(--white);
    overflow: hidden;
    box-shadow: 0 6px 18px rgba(0,0,0,0.18);
  }
  .wordmark {
    display: flex;
    align-items: center;
    gap: 14px;
    font-weight: 600;
    letter-spacing: 0.06em;
    color: var(--white);
  }
  .wordmark__square {
    width: 26px;
    height: 26px;
    background: var(--white);
  }
  .card--front .wordmark {
    position: absolute;
    top: 38px;
    left: 42px;
    font-size: 30px;
  }
  .contact {
    position: absolute;
    left: 42px;
    top: 132px;
  }
  .contact__firm {
    font-size: 22px;
    font-weight: 600;
    letter-spacing: 0.04em;
  }
  .contact__practice {
    font-size: 10px;
    letter-spacing: 0.42em;
    margin-top: 2px;
  }
  .contact__rule {
    width: 22px;
    height: 2px;
    background: var(--gold);
    margin: 12px 0 10px;
  }
  .contact__name {
    font-size: 18px;
    font-weight: 600;
    letter-spacing: 0.04em;
    text-transform: uppercase;
  }
  .contact__title {
    font-size: 14px;
    letter-spacing: 0.08em;
    margin-top: 1px;
  }
  .contact__list {
    list-style: none;
    margin-top: 14px;
    font-size: 13px;
    font-style: italic;
    letter-spacing: 0.05em;
  }
  .contact__list li {
    display: flex;
    align-items: center;
    gap: 10px;
    margin-bottom: 5px;
  }
  .contact__icon { width: 14px; height: 14px; flex: none; }
  .contact__list .contact__web { padding-left: 24px; }
  .portrait-area {
    position: absolute;
    right: 0;
    bottom: 0;
    width: 280px;
    height: 260px;
  }
  .card--back {
    display: flex;
    align-items: center;
    justify-content: center;
  }
  .card--back .wordmark { font-size: 38px; gap: 18px; }
  .card--back .wordmark__square { width: 32px; height: 32px; }
</style>
</head>
<body>
  <section class="card card--front" aria-label="Business card front">
    <div class="wordmark"><span class="wordmark__square"></span><span>OAK PARTNERS</span></div>

    <div class="contact">
      <p class="contact__firm">OAK PARTNERS</p>
      <p class="contact__practice">INJURY ATTORNEYS</p>
      <div class="contact__rule"></div>
      <p class="contact__name">Dorian Pemberton</p>
      <p class="contact__title">ATTORNEY</p>
      <ul class="contact__list">
        <li>
          <svg class="contact__icon" viewBox="0 0 16 16" aria-hidden="true">
            <path fill="var(--gold)" d="M3.6 1.5l2.2 2.6-1.3 1.6a9 9 0 0 0 5.8 5.8l1.6-1.3 2.6 2.2-1.4 2.1C7 14.6 1.4 9 1.5 2.9z"/>
          </svg>
          <span>800-555-0147</span>
        </li>
        <li>
          <svg class="contact__icon" viewBox="0 0 16 16" aria-hidden="true">
            <rect x="1" y="3" width="14" height="10" fill="var(--gold)"/>
            <path d="M1 3l7 6 7-6" fill="none" stroke="var(--navy)" stroke-width="1.4"/>
          </svg>
          <span>dorian@oakpartners.example</span>
        </li>
        <li class="contact__web"><span>www.oakpartners.example</span></li>
      </ul>
    </div>

    <svg class="portrait-area" viewBox="0 0 280 260" role="img" aria-label="Silhouettes of two standing attorneys against a light backdrop">
      <defs>
        <linearGradient id="portraitTone" x1="0" y1="0" x2="1" y2="1">
          <stop offset="0" stop-color="var(--paper)"/>
          <stop offset="1" stop-color="#c9cede"/>
        </linearGradient>
      </defs>
      <path d="M70 0 H280 V260 H0 C40 200 60 120 70 0 Z" fill="url(#portraitTone)"/>
    </svg>
  </section>

  <section class="card card--back" aria-label="Business card back">
    <div class="wordmark"><span class="wordmark__square"></span><span>OAK PARTNERS</span></div>
  </section>
</body>
</html>
```